LEARN Business Skills so you can Earn a good living

size of the poster is 8”x 10.75" plus 0.25" bleed.
Please leave 1 inch on the bottoum for footer
I want a design a poster that will attract people's attention.
I appreciate a creative ad however the ad should not take away from being able to clearly read the text.
-I also appreciate a simple creative ad that is not too busy.
-you can use graphics, vectors, or pictures of real people.
-however, if you use real people it should be a white male that is wearing a white shirt and look like a professional person.

Target Market(s)

Potential young business people

Industry/Entity Type

education

Requirements
Must have
• easy to read the text
Nice to have
• I would like a "creative" simple ad that is easy to be read
Should not have
• pictures of women

```html
<!DOCTYPE html>
<html lang="en">
<head>
<meta charset="UTF-8">
<title>Learn to Earn – Business Enrichment Course</title>
<link href="https://fonts.googleapis.com/css2?family=Poppins:wght@400;500;600;700;800&display=swap" rel="stylesheet">
<style>
  :root{
    --stage:#f3f3f3;
    --navy-top:#123a57;
    --navy-mid:#123551;
    --navy-bottom:#0b2340;
    --teal-light:#6cc8dc;
    --teal:#2a9fbb;
    --teal-deep:#1f86a6;
    --yellow:#f2e616;
    --white:#ffffff;
    --ice:#d7eef7;
    --sky:#8ccbe6;
  }
  *{margin:0;padding:0;box-sizing:border-box}
  html,body{width:1200px;height:1200px;overflow:hidden;background:var(--stage)}
  body{font-family:'Poppins',sans-serif;color:var(--white)}

  .poster{
    position:absolute;left:163px;top:0;width:874px;height:1200px;overflow:hidden;
    background:linear-gradient(180deg,var(--navy-top) 0%,var(--navy-mid) 45%,var(--navy-bottom) 100%);
  }
  .headline-top{
    position:absolute;left:0;right:0;top:40px;text-align:center;
    font-weight:800;font-size:126px;line-height:1;letter-spacing:-3px;
    background:linear-gradient(180deg,var(--teal-light),var(--teal-deep));
    -webkit-background-clip:text;background-clip:text;color:transparent;
    padding-left:10px;
  }
  .headline-main{
    position:absolute;left:0;right:0;top:122px;text-align:center;
    font-weight:700;font-size:218px;line-height:1;letter-spacing:-4px;color:var(--yellow);
  }
  .course-title{
    position:absolute;left:0;right:0;top:324px;text-align:center;
    font-weight:600;font-size:31px;letter-spacing:3.6px;line-height:1;
  }
  .rule{position:absolute;height:2px;background:var(--teal)}
  .rule--title{left:327px;width:214px;top:368px}
  .tagline{
    position:absolute;left:0;right:0;top:376px;text-align:center;
    font-weight:500;font-size:21px;line-height:30px;
  }
  .illustration{position:absolute;left:147px;top:425px;width:586px;height:382px}

  .skills-heading{
    position:absolute;left:0;right:0;top:830px;text-align:center;
    font-weight:600;font-size:23.5px;line-height:34px;
  }
  .skills-heading .accent{color:var(--yellow)}
  .rule--skills{left:408px;width:61px;top:871px}

  .benefit{position:absolute;top:893px;height:50px}
  .benefit__pill{
    position:absolute;left:24px;right:0;top:4px;height:44px;border-radius:22px;
    background:linear-gradient(180deg,var(--teal-light),var(--teal-deep));
    display:flex;align-items:center;padding-left:42px;
    font-weight:600;font-size:17.5px;line-height:19px;
  }
  .benefit__icon{
    position:absolute;left:0;top:-2px;width:56px;height:56px;border-radius:50%;
    background:var(--white);border:3px solid var(--navy-bottom);
    display:flex;align-items:center;justify-content:center;
  }
  .benefit--job{left:61px;width:228px}
  .benefit--business{left:321px;width:225px}
  .benefit--salary{left:576px;width:224px}

  .subject-list{
    position:absolute;left:30px;right:30px;top:969px;text-align:center;
    font-weight:400;font-size:14.6px;line-height:21.3px;letter-spacing:.1px;
  }
  .subject-list .sep{color:var(--yellow)}

  .enroll-bar{
    position:absolute;left:109px;top:1074px;width:676px;height:46px;
    background:linear-gradient(180deg,var(--teal-light),var(--teal-deep));
    border-radius:12px 18px 18px 12px;
    transform:skewX(-8deg);
  }
  .enroll-label,.enroll-phone{
    position:absolute;top:1076px;line-height:44px;font-weight:600;white-space:nowrap;
  }
  .enroll-label{left:143px;font-size:31px;letter-spacing:4.5px}
  .enroll-phone{left:500px;font-size:26px;letter-spacing:2.5px}
  .enroll-call{
    position:absolute;left:412px;top:1065px;width:64px;height:64px;border-radius:50%;
    background:var(--white);border:4px solid var(--navy-bottom);
    display:flex;align-items:center;justify-content:center;
  }
  .website{
    position:absolute;left:0;right:0;top:1130px;text-align:center;
    font-weight:500;font-size:16.5px;letter-spacing:4.3px;line-height:28px;
  }
  .website .accent{color:var(--yellow)}
</style>
</head>
<body>
<main class="poster">
  <div class="headline-top">LEARN TO</div>
  <div class="headline-main">EARN</div>
  <div class="course-title">BUSINESS ENRICHMENT COURSE</div>
  <div class="rule rule--title"></div>
  <p class="tagline">A proven success of helping people in their livelihoods</p>

  <svg class="illustration" viewBox="0 0 586 382" role="img" aria-label="Illustration of online learning: a smartphone showing a video lesson with an instructor, a student with a laptop sitting on books, an open book, a light bulb and leafy plants">
    <defs>
      <linearGradient id="illo-fill" x1="0" y1="0" x2="0" y2="1">
        <stop offset="0" stop-color="#d7eef7"/>
        <stop offset="1" stop-color="#8ccbe6"/>
      </linearGradient>
    </defs>
    <path d="M40 380 C10 360 0 300 60 260 C70 200 20 150 60 100 C100 50 170 60 200 70 C210 40 230 30 290 30 C340 30 360 0 400 10 C460 20 470 70 500 110 C540 150 520 200 560 240 C600 290 580 350 540 375 Z" fill="url(#illo-fill)" opacity=".92"/>
  </svg>

  <h2 class="skills-heading"><span class="accent">BUSINESS SKILLS</span> THAT WILL HELP YOU</h2>
  <div class="rule rule--skills"></div>

  <div class="benefit benefit--job">
    <div class="benefit__pill">Get a quality job</div>
    <div class="benefit__icon">
      <svg width="28" height="30" viewBox="0 0 28 30" aria-hidden="true">
        <path d="M8 16 L3 27 L8 25 L10 29 L14 20 L18 29 L20 25 L25 27 L20 16 Z" fill="#0b2340"/>
        <circle cx="14" cy="11" r="10" fill="#0b2340"/>
        <circle cx="14" cy="11" r="6.5" fill="#fff"/>
        <path d="M14 6.5 L15.3 9.5 L18.5 9.7 L16 11.8 L16.8 15 L14 13.2 L11.2 15 L12 11.8 L9.5 9.7 L12.7 9.5 Z" fill="#0b2340"/>
      </svg>
    </div>
  </div>
  <div class="benefit benefit--business">
    <div class="benefit__pill">Start/Grow<br>your business</div>
    <div class="benefit__icon">
      <svg width="28" height="26" viewBox="0 0 28 26" aria-hidden="true">
        <rect x="2" y="16" width="4" height="9" fill="#0b2340"/>
        <rect x="8" y="12" width="4" height="13" fill="#0b2340"/>
        <rect x="14" y="14" width="4" height="11" fill="#0b2340"/>
        <rect x="20" y="9" width="4" height="16" fill="#0b2340"/>
        <path d="M2 12 L9 5 L15 9 L24 2" stroke="#0b2340" stroke-width="2.5" fill="none"/>
        <path d="M19 1 L26 0 L25 7 Z" fill="#0b2340"/>
      </svg>
    </div>
  </div>
  <div class="benefit benefit--salary">
    <div class="benefit__pill">Increase your<br>salary</div>
    <div class="benefit__icon">
      <svg width="28" height="30" viewBox="0 0 28 30" aria-hidden="true">
        <text x="14" y="9" text-anchor="middle" font-family="Poppins,sans-serif" font-weight="700" font-size="11" fill="#0b2340">$</text>
        <rect x="5" y="12" width="18" height="3" fill="#0b2340"/>
        <rect x="3" y="17" width="22" height="3" fill="#0b2340"/>
        <rect x="1" y="22" width="26" height="3" fill="#0b2340"/>
        <path d="M14 15 L20 21 L16.5 21 L16.5 28 L11.5 28 L11.5 21 L8 21 Z" fill="#0b2340" stroke="#fff" stroke-width="1"/>
      </svg>
    </div>
  </div>

  <p class="subject-list">
    BUSINESS ADMIISTRATION <span class="sep">|</span> SMALL BUSINESS MANAGEMENT <span class="sep">|</span> FINANCE <span class="sep">|</span> INVESTMENTS <span class="sep">|</span> COMPUTERS <span class="sep">|</span><br>
    ACCOUNTING <span class="sep">|</span> SALES &nbsp;MARKETING <span class="sep">|</span> PROJECT MANAGEMENT INTERVIEWING SKILLS <span class="sep">|</span> BUSINESS LAW <span class="sep">|</span><br>
    NEGOTIATION <span class="sep">|</span> PUBLIC SPEAKING <span class="sep">|</span> IMPORT/EXPORT <span class="sep">|</span> INFORMATION TECHNOLOY <span class="sep">|</span> DISTRIBUTION <span class="sep">|</span><br>
    MARKETING &nbsp;<span class="sep">|</span> &nbsp; LEDGERPRO <span class="sep">|</span> REAL ESTATE <span class="sep">|</span> HEALTH CARE <span class="sep">|</span> MANAGEMENT <span class="sep">|</span> MARKETHUB
  </p>

  <div class="enroll-bar"></div>
  <div class="enroll-label">ENROLL NOW</div>
  <div class="enroll-call">
    <svg width="30" height="30" viewBox="0 0 24 24" aria-hidden="true">
      <path d="M6.6 10.8c1.4 2.8 3.8 5.1 6.6 6.6l2.2-2.2c.3-.3.7-.4 1-.2 1.1.4 2.3.6 3.6.6.6 0 1 .4 1 1V20c0 .6-.4 1-1 1C10.6 21 3 13.4 3 4c0-.6.4-1 1-1h3.5c.6 0 1 .4 1 1 0 1.3.2 2.5.6 3.6.1.3 0 .7-.2 1z" fill="#0b2340"/>
    </svg>
  </div>
  <div class="enroll-phone">011 555 010 2020</div>

  <p class="website">www.<span class="accent">learnearnacademy</span>.com</p>
</main>
</body>
</html>
```